New Property development signage

large poster for a new development.
3 metres x 2 metres. To include the following.

Tresswick Gardens
TO LET
LUXURY FULLY FURNISHED LARGE
2 AND 3 BED APARTMENTS
Garrold Estates
362 4150
www.garroldestates-example.com

Need this to be large simple writing with Garrold estates logo on the bottom

Target Market(s)

High end rental property market

Industry/Entity Type

Real Estate Development

Colors
000000
cbcbcb
0555a3

Requirements
Must have
• Name of the development must be in a different font, classic style
Nice to have
• Light Grey background, blues for colours
Should not have
• anymore than 3 /4 colours

```html
<!DOCTYPE html>
<html lang="en">
<head>
<meta charset="utf-8">
<title>Tresswick Gardens – To Let</title>
<link rel="stylesheet" href="https://fonts.googleapis.com/css2?family=Bebas+Neue&family=Montserrat:wght@800&family=Oswald:wght@500;700&family=Playfair+Display:wght@700&display=swap">
<style>
  :root {
    --brand-blue: #283a8e;
    --paper: #ffffff;
    --edge: #cbcbcb;
  }
  * { margin: 0; padding: 0; box-sizing: border-box; }
  html, body { width: 1200px; height: 2396px; overflow: hidden; background: var(--paper); }
  .sign {
    position: relative;
    width: 1200px;
    height: 2396px;
    background: var(--paper);
    border: 4px solid var(--edge);
  }
  .headline-band {
    position: absolute;
    left: 28px; top: 28px;
    width: 1136px; height: 324px;
    background: var(--brand-blue);
    display: flex; align-items: center; justify-content: center;
  }
  .headline-band h1 {
    font-family: "Montserrat", sans-serif;
    font-weight: 800;
    font-size: 250px;
    letter-spacing: -6px;
    color: var(--paper);
    line-height: 1;
  }
  .feature {
    position: absolute;
    left: 0; width: 100%;
    text-align: center;
    font-family: "Bebas Neue", sans-serif;
    font-size: 140px;
    color: var(--brand-blue);
    line-height: 1;
    white-space: nowrap;
    transform: translateY(-50%);
  }
  .development-name {
    position: absolute;
    left: 0; width: 100%;
    text-align: center;
    font-family: "Playfair Display", serif;
    font-weight: 700;
    font-size: 118px;
    color: var(--brand-blue);
    line-height: 1;
    white-space: nowrap;
    transform: translateY(-50%);
  }
  .divider {
    position: absolute;
    left: 28px; width: 1136px; height: 5px;
    background: var(--brand-blue);
  }
  .agent-mark {
    position: absolute;
    left: 36px; top: 2060px;
    font-family: "Oswald", sans-serif;
    color: var(--brand-blue);
    white-space: nowrap;
  }
  .agent-mark__name {
    display: flex; align-items: center; gap: 16px;
    font-weight: 700;
    font-size: 60px;
    line-height: 1;
  }
  .agent-mark__square {
    width: 48px; height: 48px;
    background: var(--brand-blue);
    flex: none;
  }
  .agent-mark__services {
    margin-top: 22px;
    font-weight: 500;
    font-size: 22px;
    letter-spacing: 0.5px;
  }
  .contact {
    position: absolute;
    right: 36px; top: 2050px;
    text-align: right;
    font-family: "Oswald", sans-serif;
    color: var(--brand-blue);
    white-space: nowrap;
  }
  .contact__phone { font-weight: 700; font-size: 100px; line-height: 1; }
  .contact__web { margin-top: 18px; font-weight: 700; font-size: 34px; line-height: 1; }
</style>
</head>
<body>
  <main class="sign">
    <header class="headline-band"><h1>TOLET</h1></header>

    <p class="feature" style="top:570px">LUXURY FULLY FURNISHED</p>
    <div class="divider" style="top:690px"></div>

    <p class="feature" style="top:820px">LARGE 2 AND 3 BED</p>
    <p class="feature" style="top:965px">APARTMENTS</p>
    <div class="divider" style="top:1090px"></div>

    <p class="development-name" style="top:1235px">Tresswick Gardens</p>
    <div class="divider" style="top:1380px"></div>

    <p class="feature" style="top:1550px">WITH BALCONIES</p>
    <p class="feature" style="top:1710px">AND GARDENS</p>

    <div class="agent-mark">
      <div class="agent-mark__name"><span class="agent-mark__square"></span>Garrold Estates</div>
      <div class="agent-mark__services">Sales • Lettings • Management • B.E.R. Certs</div>
    </div>

    <div class="contact">
      <div class="contact__phone">PH: 362 4150</div>
      <div class="contact__web">www.garroldestates-example.com</div>
    </div>
  </main>
</body>
</html>
```